Brochure for a website accessibility report

This brochure is related to a report that www.qelvantrix.org sell. The report shows the results of an automated audit of a websites accessibility. It shows details of issues found with screen shots, examples of code and provides remediation advice.

The brochure will be a pdf 8.5 inches by 11 inches. It can be anywhere from 6 to 10 pages.

The FlintVue™ name itself should be “Bree Serif” font. The fonts, styles, colors and sizes are up to you.

The images used and logo of the Office of Digital Reachworks and K7P logo are upload

We highlighted in blue page extracts from the report we sell. Do not use the blue highlight, it is merely there to show you where the specific examples of the report we sell are vs the other content in the report. The areas in blue which show the content from the actual report should be shown as an extract of the actual page of the report. You have flexibility to change the layout and the way the content look.

The red square callouts over the blue content are callouts that describe the specific page extracts. We used it as a red callout only so that you would be able to see it. You should change the specific location, look and feel of the callout to be appropriate

Target Market(s)

Marketing and Technical people

Industry/Entity Type

Information Technology

Font styles to use
Sans Serif

Colors

Designer to choose colors to be used in the design.

Requirements
Should not have
• wheelchairs, images of blind people

```html
<!DOCTYPE html>
<html lang="en">
<head>
<meta charset="utf-8">
<title>Accessibility Report Brochure – Cover Spread</title>
<link rel="stylesheet" href="https://fonts.googleapis.com/css2?family=Bree+Serif&family=Montserrat:wght@400;600&display=swap">
<style>
  :root {
    --backdrop: #a7a8ac;
    --paper: #f4f4f4;
    --brand-green: #27a468;
    --charcoal: #3b3b3d;
    --charcoal-light: #5a5a5d;
    --photo-light: #cfcfcf;
    --photo-dark: #4a4a4a;
    --ink: #2b2b2b;
    --white: #ffffff;
  }
  * { box-sizing: border-box; margin: 0; padding: 0; }
  html, body {
    width: 1200px; height: 900px; overflow: hidden;
    background: var(--backdrop);
    font-family: "Montserrat", Arial, sans-serif;
  }
  .spread {
    position: absolute; left: 28px; top: 80px;
    width: 1144px; height: 740px;
    display: flex;
    box-shadow: 0 14px 30px rgba(0,0,0,0.25);
  }
  .page {
    position: relative; width: 572px; height: 740px;
    background: var(--paper); overflow: hidden;
  }
  .page--back { box-shadow: inset -10px 0 14px -10px rgba(0,0,0,0.25); }
  .page--front { box-shadow: inset 10px 0 14px -10px rgba(0,0,0,0.25); }
  .page-shapes, .photo { position: absolute; left: 0; top: 0; width: 572px; height: 740px; }

  .contact {
    position: absolute; left: 44px; top: 612px; color: var(--white);
  }
  .contact__title {
    font-family: "Montserrat", Arial, sans-serif; font-weight: 600;
    font-size: 15px; letter-spacing: 4px; margin-bottom: 8px;
  }
  .contact__line { font-size: 9.5px; line-height: 13px; opacity: 0.92; }
  .contact__gap { height: 10px; }
  .web-address {
    position: absolute; right: 60px; top: 672px;
    color: var(--white); font-size: 9.5px; letter-spacing: 0.5px;
  }

  .brand {
    position: absolute; left: 330px; top: 350px;
    display: flex; align-items: center; gap: 10px;
  }
  .brand__square { width: 26px; height: 26px; background: var(--brand-green); flex: none; }
  .brand__name {
    font-family: "Bree Serif", Georgia, serif; font-size: 15px; line-height: 16px;
    color: var(--ink); text-transform: uppercase; width: 150px;
  }
  .cover-title {
    position: absolute; left: 38px; top: 452px; color: var(--white);
  }
  .cover-title__main {
    font-family: "Bree Serif", Georgia, serif; font-size: 44px;
    letter-spacing: 5px; line-height: 1;
  }
  .cover-title__sub {
    font-family: "Montserrat", Arial, sans-serif; font-size: 7.5px;
    letter-spacing: 3.2px; text-transform: uppercase; margin-top: 6px; opacity: 0.9;
  }
</style>
</head>
<body>
  <main class="spread">
    <section class="page page--back">
      <svg class="page-shapes" viewBox="0 0 572 740" aria-hidden="true">
        <polygon points="250,450 572,395 572,455 420,470" fill="var(--charcoal)"/>
        <polygon points="0,560 572,625 572,740 0,740" fill="var(--brand-green)"/>
      </svg>
      <svg class="photo" viewBox="0 0 572 740" role="img" aria-label="Black-and-white photo of schoolchildren at a rally">
        <defs>
          <linearGradient id="backPhoto" x1="0" y1="0" x2="1" y2="1">
            <stop offset="0" stop-color="var(--photo-light)"/>
            <stop offset="1" stop-color="var(--photo-dark)"/>
          </linearGradient>
        </defs>
        <polygon points="250,130 572,130 572,395 250,450" fill="url(#backPhoto)"/>
      </svg>
      <div class="contact">
        <h2 class="contact__title">CONTACT</h2>
        <p class="contact__line">Headquarters</p>
        <p class="contact__line">Office of Digital Reachworks</p>
        <p class="contact__line">4800 Linden Court #214</p>
        <p class="contact__line">Marlow Heights, VA 20184</p>
        <div class="contact__gap"></div>
        <p class="contact__line">Phone: 410-555-0172</p>
        <p class="contact__line">Email: hello@qelvantrix.org</p>
      </div>
      <p class="web-address">www.qelvantrix.org</p>
    </section>

    <section class="page page--front">
      <svg class="photo" viewBox="0 0 572 740" role="img" aria-label="Black-and-white photo of children holding a hand-painted peace sign">
        <defs>
          <linearGradient id="frontPhoto" x1="0" y1="0" x2="0.8" y2="1">
            <stop offset="0" stop-color="var(--photo-light)"/>
            <stop offset="0.6" stop-color="#8a8a8a"/>
            <stop offset="1" stop-color="var(--photo-dark)"/>
          </linearGradient>
        </defs>
        <polygon points="0,0 572,0 572,250 300,430 0,410" fill="url(#frontPhoto)"/>
      </svg>
      <svg class="page-shapes" viewBox="0 0 572 740" aria-hidden="true">
        <polygon points="0,410 300,430 572,448 0,565" fill="var(--charcoal)"/>
        <polygon points="300,430 572,448 572,470" fill="var(--charcoal-light)"/>
      </svg>
      <div class="brand">
        <span class="brand__square"></span>
        <span class="brand__name">Office of Digital Reachworks</span>
      </div>
      <div class="cover-title">
        <h1 class="cover-title__main">REPORT</h1>
        <p class="cover-title__sub">Office of Digital Reachworks</p>
      </div>
    </section>
  </main>
</body>
</html>
```